Simple Logo Design for Semi-Clear Plastic Frosted Card stock

Create a business card on frosted plastic. compliment existing logo elements with a tree trunk, roots, or seed at the lower half and the full logo both on the front.

Contact information will go on a solid portion of the back of this design since this card stock is semi-transparent.

It is important to consider this plastic card stock medium in your design. I found helpful tips and guides listed at vellaprint-sample.net: be careful to understand ink printed on plastic cards cannot have too much of a consistent print area or risks peeling and fine lines can easily scratch off.
Updates

2" x 3.5" 20PT Clear Plastic Business cards with Round corners Please get info or templates here: https://www.vellaprint-sample.net/product-detail/2-x-35-20pt-clear-plastic-business-cards-with-round-corners

Target Market(s)

Not for profit- religion

Industry/Entity Type

Business

Must include complementary elements to the existing logo

Font styles to use
Decorative

Colors
000000

Requirements
Must have
• Elements of community, nature and oneness. Such as: seed, roots, tree trunk, etc.
• Three lines of space on the back for Name, Title, Phone Number.
Nice to have
• I like a light use of decorative elements
Should not have
• No eyes, from faces or animals.

```html
<!DOCTYPE html>
<html lang="en">
<head>
<meta charset="utf-8">
<title>Steadfast Grove – Business Card</title>
<link rel="stylesheet" href="https://fonts.googleapis.com/css2?family=Open+Sans:wght@400;600&display=swap">
<style>
  :root {
    --page-bg: #d9d6d1;
    --frost: #e6eae8;
    --frost-edge: #f4f6f5;
    --deep-teal: #0f3b35;
    --teal-light: #2d5f5a;
    --leaf-green: #2f7a2c;
    --name-ink: #dcecef;
    --detail-ink: #eef5f6;
    --brand-ink: #1d4a22;
  }
  * { margin: 0; padding: 0; box-sizing: border-box; }
  html, body {
    width: 1200px;
    height: 969px;
    overflow: hidden;
    background: var(--page-bg);
    font-family: "Open Sans", Arial, sans-serif;
  }
  .card {
    position: absolute;
    left: 100px;
    top: 200px;
    width: 1000px;
    height: 568px;
    border-radius: 26px;
    overflow: hidden;
    background: linear-gradient(160deg, var(--frost-edge), var(--frost) 60%, #dde2e0);
    box-shadow: 0 10px 30px rgba(0,0,0,0.18);
  }
  .card-art {
    position: absolute;
    inset: 0;
    width: 100%;
    height: 100%;
  }
  .contact {
    position: absolute;
    left: 66px;
    top: 56px;
    color: var(--detail-ink);
  }
  .contact-name {
    font-size: 38px;
    font-weight: 600;
    letter-spacing: 1px;
    color: var(--name-ink);
    line-height: 1.2;
  }
  .contact-title {
    font-size: 31px;
    font-weight: 400;
    letter-spacing: 1px;
    line-height: 1.4;
  }
  .contact-phone {
    margin-top: 22px;
    font-size: 31px;
    font-weight: 400;
    letter-spacing: 1px;
  }
  .brand {
    position: absolute;
    left: 520px;
    top: 310px;
    width: 430px;
    display: flex;
    flex-direction: column;
    align-items: center;
    gap: 22px;
  }
  .brand-dot {
    width: 120px;
    height: 120px;
    border-radius: 50%;
    background: var(--brand-ink);
  }
  .brand-name {
    font-size: 44px;
    font-weight: 600;
    color: var(--brand-ink);
    letter-spacing: 1px;
    white-space: nowrap;
  }
</style>
</head>
<body>
  <div class="card">
    <svg class="card-art" viewBox="0 0 1000 568" preserveAspectRatio="none" aria-hidden="true">
      <defs>
        <linearGradient id="tealPanel" x1="0" y1="0" x2="1" y2="1">
          <stop offset="0" stop-color="var(--teal-light)"/>
          <stop offset="0.55" stop-color="var(--deep-teal)"/>
          <stop offset="1" stop-color="#0b2e29"/>
        </linearGradient>
      </defs>
      <path class="teal-panel" fill="url(#tealPanel)"
            d="M0,0 H790 C705,140 620,230 460,272 C260,322 75,380 12,568 H0 Z"/>
      <path class="green-sweep" fill="none" stroke="var(--leaf-green)" stroke-width="9"
            d="M806,0 C720,152 632,244 468,288 C272,338 92,396 30,568"/>
    </svg>

    <div class="contact">
      <p class="contact-name">ALAN MARSH</p>
      <p class="contact-title">PRESIDENT</p>
      <p class="contact-phone">555 0142 7780</p>
    </div>

    <div class="brand">
      <span class="brand-dot"></span>
      <p class="brand-name">STEADFAST GROVE</p>
    </div>
  </div>
</body>
</html>
```